Quality Monitoring Company Needs a New Site

We are an established company that has a fair number of clients but the site lacks current design standards that we'd like to keep up with. We'd like to mimic the same style of the site on plinkora.com, vetrumo.com, https://brindlecoffer.com/, etc. We'd also like to make sure the designer understands SEO Silos and how it effects the design elements. Attached is the structure that I'd like to follow for the pages. You don't need to design every single sub-page because they'll probably be fairly similar; however, I want to see at least 1 each. Please use the content on our current site for filler areas. Please try to do a good job of understanding what we do so you can use your best judgement on what is needed to be successful. Use our color scheme and the logo should be the side view but I included the AI just in case.
Updates

I am narrowing down on the field of designs that I have received. There are a lot of similarities between the designs I like and don't like. I'd also like to ensure that some of the inner pages get done in the next 5 days so I can see the creativity that is there as well. That is probably what is next -- getting a few inner pages completed so I can see what you can come up with (not based on our current website) because the current "front pages" are all so good and so close.

Industry/Entity Type

Telecommunications

Colors

Designer to choose colors to be used in the design.

Requirements
Must have
• SEO Silo Look and Feel
• Current Colors
Should not have
• No stockphotos whatsoever. NONE.

```html
<!DOCTYPE html>
<html lang="en">
<head>
<meta charset="utf-8">
<title>DialMetric – Homepage Variations</title>
<link href="https://fonts.googleapis.com/css2?family=Montserrat:wght@400;600;700&family=Roboto:wght@400;500&display=swap" rel="stylesheet">
<style>
:root{
  --navy:#0c2d57;
  --blue:#0aa5e2;
  --ink:#333a44;
  --muted:#7a808a;
  --line:#e3e6ea;
  --foot:#f5f6f7;
}
*{box-sizing:border-box}
html,body{margin:0;width:869px;height:1200px;overflow:hidden;background:#fff}
body{position:relative;font-family:'Roboto',sans-serif;color:var(--ink)}
h1,h2,p,ul{margin:0}
.page{position:absolute;top:22px;width:279px;height:1157px;background:#fff;box-shadow:0 0 3px rgba(0,0,0,.18);overflow:hidden}
.page>*{position:absolute}
.v1{left:13px}.v2{left:296px}.v3{left:579px}

.hero-bg{left:0;top:0;width:279px;height:150px}
.logo{left:21px;top:4px;font:600 10px/12px 'Montserrat',sans-serif;color:var(--navy);letter-spacing:-.2px}
.nav{left:84px;top:9px;display:flex;gap:7px;font-size:3.3px;line-height:4px;color:var(--ink)}
.nav .active{font-weight:500;color:var(--navy)}
.register{left:220px;top:6px;width:39px;height:9px;background:var(--navy);color:#fff;font:500 3.2px 'Roboto',sans-serif;display:flex;align-items:center;justify-content:center;border-radius:1px}
.hero-title{left:21px;top:50px;font:600 15px/17px 'Montserrat',sans-serif;color:var(--navy);white-space:nowrap}
.hero-copy{left:21px;top:68px;width:92px;font-size:3.4px;line-height:8px}
.btn{height:11px;border-radius:6px;background:var(--blue);color:#fff;font:600 3.6px 'Montserrat',sans-serif;display:flex;align-items:center;justify-content:center;gap:2px;box-shadow:0 1px 3px rgba(10,165,226,.35)}
.btn i{width:3px;height:3px;border-radius:50%;background:#fff;display:block}
.btn.dark{background:var(--navy);box-shadow:0 1px 3px rgba(12,45,87,.35)}
.btn.sq{border-radius:0;box-shadow:none}
.hero-btn{left:21px;top:95px;width:50px}
.hero-art{left:129px;top:35px;width:130px;height:86px;border-radius:3px;background:linear-gradient(160deg,#e6e9ee,#f7d0c4 55%,#3a3f4a)}
.mouse{left:136px;top:135px;width:6px;height:14px}

.h2{font:600 8.5px/10px 'Montserrat',sans-serif;color:var(--navy)}
.h2 span{font-weight:400;color:var(--blue)}
.center{left:0;width:279px;text-align:center}
.copy{font-size:3.1px;line-height:8.2px;color:var(--ink);text-align:justify}
.copy.c{text-align:center}

.welcome-title{top:167px}
.welcome-copy{left:30px;top:182px;width:219px}
.ind-title{left:21px;top:213px}
.ind-copy{left:21px;top:228px;width:114px}
.ind-btn{left:21px;top:280px;width:50px}
.ind-art{left:139px;top:207px;width:120px;height:91px;border-radius:30% 8% 6px 6px;background:linear-gradient(135deg,#eef0f3,#dfe3e8 50%,#a2527f)}
.srv-art{left:30px;top:332px;width:96px;height:84px;border-radius:6px;background:linear-gradient(150deg,#dbe7f3,#6fb0e6 45%,#f4c3a0 70%,#2c3d5a)}
.srv-title{left:144px;top:335px}
.srv-copy{left:144px;top:348px;width:114px}
.srv-btn{left:144px;top:402px;width:50px}
.team-title{left:21px;top:464px}
.team-copy{left:21px;top:477px;width:114px}
.team-btn{left:21px;top:529px;width:50px}
.team-art{left:146px;top:455px;width:108px;height:100px;border-radius:6px;background:linear-gradient(140deg,#dcebf5,#1aa8e3 45%,#0c2d57 80%)}

.price-title{top:592px}
.price-copy{left:40px;top:607px;width:199px}
.tier{top:637px;width:75px;height:124px;background:#fff;border:.5px solid var(--line);display:flex;flex-direction:column;align-items:center}
.tier.t1{left:22px}
.tier.gold{left:97px;top:632px;width:83px;height:135px;box-shadow:0 0 4px rgba(0,0,0,.12);z-index:2}
.tier.plat{left:180px;width:76px}
.tier-head{width:100%;height:22px;flex:none;background:var(--navy);color:#fff;font:600 5.4px 'Montserrat',sans-serif;display:flex;align-items:center;justify-content:center;position:relative}
.gold .tier-head{height:24px;background:var(--blue)}
.tier-head.wave{background:none;height:27px;align-items:flex-start;padding-top:8px}
.gold .tier-head.wave{background:none}
.tier-head.wave svg{position:absolute;inset:0;width:100%;height:100%}
.tier-head.wave b{position:relative;font-weight:600}
.price{font:400 6.2px 'Roboto',sans-serif;color:var(--muted);margin-top:6px}
.gold .price{color:var(--blue)}
.sub{font-size:4px;color:var(--muted)}
.feats{list-style:none;margin:4px 0 0;padding:0;font-size:3.2px;color:var(--ink)}
.feats li{display:flex;align-items:center;gap:4px;height:8.2px}
.feats svg{width:3.4px;height:3.4px;flex:none}
.t1 .feats svg{stroke:var(--blue)}
.note{font-size:3.5px;color:var(--muted);text-align:center;line-height:5.5px;margin-top:3px}
.tier .btn{width:42px;height:11px;margin-top:auto;margin-bottom:10px;font-size:3.4px;flex:none}

.blog-title{top:799px;font-size:12px;line-height:14px}
.card{top:824px;width:73px;height:95px;border:.5px solid var(--line);background:#fff}
.card>*{position:absolute}
.card.b1{left:21px}.card.b2{left:102px}.card.b3{left:184px}
.card-img{left:0;top:0;width:100%;height:50px}
.b1 .card-img{background:linear-gradient(135deg,#d9dde3,#8c7a6a 60%,#2e3136)}
.b2 .card-img{background:linear-gradient(135deg,#f2f4f6,#cfe3f2 60%,#8fb9d8)}
.b3 .card-img{background:linear-gradient(135deg,#9bb7a6,#4d5560 60%,#2b2f36)}
.card-copy{left:6px;top:55px;width:62px;font-size:2.8px;line-height:5.6px;color:var(--muted)}
.avatar{left:6px;top:72px;width:9px;height:9px;border-radius:50%;background:#c9ced6}
.author{left:18px;top:75px;font-size:2.8px;color:var(--ink)}
.card .btn{left:40px;top:81px;width:29px;height:9px;font-size:2.8px}

.contact-title{left:21px;top:955px}
.field{left:21px;width:104px;height:8px;background:#fff;box-shadow:0 1px 3px rgba(0,0,0,.12);font-size:2.6px;line-height:3px;color:var(--muted);padding:2.4px 3px}
.f1{top:973px}.f2{top:984px}.f3{top:996px}.f4{top:1007px}
.f5{top:1019px;height:22px}
.submit{left:21px;top:1043px;width:42px;height:11px}
.touch-title{left:155px;top:955px}
.touch-copy{left:155px;top:970px;width:104px}
.info{left:155px;top:1004px;font-size:3.3px;line-height:4.6px}
.info div{margin-bottom:2.6px}
.info strong{display:flex;align-items:center;gap:2px;font-weight:500;color:var(--navy)}
.info svg{width:3.2px;height:3.2px;fill:var(--navy)}
.info span{display:block;padding-left:6px;font-size:3px;color:var(--ink)}

.footer{left:0;top:1074px;width:279px;height:83px;background:var(--foot)}
.footer>*{position:absolute}
.f-logo{left:21px;top:25px;font:600 10px/12px 'Montserrat',sans-serif;color:var(--navy)}
.social{left:34px;top:38px;display:flex;gap:1.5px}
.social i{width:5px;height:5px;border-radius:50%;border:.5px solid var(--navy);display:block}
.f-h{font:600 3.6px/4.5px 'Montserrat',sans-serif;color:var(--navy)}
.news{left:86px;top:13px;width:61px}
.news p{font-size:2.3px;line-height:3.3px;color:var(--muted);margin:2px 0 4px}
.news .in{height:8px;background:#fff;border:.4px solid var(--line);font-size:2.3px;line-height:3px;color:var(--muted);padding:2.4px 3px}
.news .btn{width:28px;height:7px;font-size:2.5px;margin-top:4px;border-radius:0;box-shadow:none}
.fcontact{left:165px;top:13px}
.fcontact div{display:flex;gap:3px;font-size:2.6px;line-height:3.6px;margin-top:2px;color:var(--ink)}
.fcontact svg{width:3px;height:3px;fill:var(--blue);flex:none;margin-top:.3px}
.links{left:231px;top:13px}
.links ul{list-style:none;margin:3px 0 0;padding:0;font-size:2.6px;line-height:6px;color:var(--ink)}
.copyright{left:0;width:279px;top:75px;text-align:center;font-size:2.8px;color:var(--ink)}
.nav.on-blue span:nth-child(n+3){color:#e8f6fd}
.v3 .hero-title,.v3 .hero-copy{color:#fff}
</style>
</head>
<body>

<!-- Variation 1 -->
<section class="page v1">
  <div class="logo">DialMetric</div>
  <nav class="nav"><span class="active">Home</span><span>Industries</span><span>Services</span><span>Pricing</span><span>Team</span><span>Blog</span><span>Contact Us</span></nav>
  <div class="register">Register / Login</div>
  <h1 class="hero-title">DialMetric</h1>
  <p class="hero-copy">Sed ut perspiciatis unde omnis iste natus error voluptatem accusantium doloremque eatae vitae dicta sunt explicabo.</p>
  <div class="btn hero-btn">Get Started <i></i></div>
  <div class="hero-art" role="img" aria-label="Illustration of an agent working at a laptop beside floating screens"></div>
  <svg class="mouse" viewBox="0 0 6 14"><rect x="1" y="0.5" width="4" height="7" rx="2" fill="none" stroke="#333" stroke-width=".5"/><path d="M1.5 10l1.5 1.5 1.5-1.5" fill="none" stroke="#333" stroke-width=".5"/></svg>

  <h2 class="h2 center welcome-title">Welcome to <span>DialMetric</span></h2>
  <p class="copy c welcome-copy">Sed ut perspiciatis unde omnis iste natus error sit voluptatem accusantium doloremque laudantium, totam rem aperiam, eaque ipsa quae ab illo inventore veritatis et quasi architecto beatae vitae dicta sunt explicabo.</p>

  <h2 class="h2 ind-title">Our <span>Industries</span></h2>
  <p class="copy ind-copy">Sed ut perspiciatis unde omnis iste natus error sit voluptatem accusantium doloremque laudantium, totam rem aperiam, eaque ipsa quae ab illo inventore veritatis et quasi architecto beatae vitae dicta sunt explicabo. Nemo enim ipsam voluptatem quia voluptas sit aspernatur aut odit aut fugit, sed quia consequuntur magni dolores eos qui nesciunt.</p>
  <div class="btn ind-btn">Read More <i></i></div>
  <div class="ind-art" role="img" aria-label="Illustration of a woman at a laptop in front of a large monitor"></div>

  <div class="srv-art" role="img" aria-label="Illustration of a support agent with headset surrounded by service icons"></div>
  <h2 class="h2 srv-title">Our <span>Services</span></h2>
  <p class="copy srv-copy">Sed ut perspiciatis unde omnis iste natus error sit voluptatem accusantium doloremque laudantium, totam rem aperiam, eaque ipsa quae ab illo inventore veritatis et quasi architecto beatae vitae dicta sunt explicabo. Nemo enim ipsam voluptatem quia voluptas sit aspernatur aut odit aut fugit, sed quia consequuntur magni dolores eos qui nesciunt.</p>
  <div class="btn srv-btn">View More <i></i></div>

  <h2 class="h2 team-title">Our <span>Team</span></h2>
  <p class="copy team-copy">Sed ut perspiciatis unde omnis iste natus error sit voluptatem accusantium doloremque laudantium, totam rem aperiam, eaque ipsa quae ab illo inventore veritatis et quasi architecto beatae vitae dicta sunt explicabo. Nemo enim ipsam voluptatem quia voluptas sit aspernatur aut odit aut fugit, sed quia consequuntur magni dolores eos qui nesciunt.</p>
  <div class="btn team-btn">View More <i></i></div>
  <div class="team-art" role="img" aria-label="Illustration of team member portraits arranged around a circle"></div>

  <h2 class="h2 center price-title">Our <span>Pricing</span></h2>
  <p class="copy c price-copy">Sed ut perspiciatis unde omnis iste natus error sit voluptatem accusantium doloremque laudantium, totam rem aperiam, eaque ipsa quae ab illo inventore veritatis et quasi architecto beatae vitae dicta sunt explicabo.</p>
  <div class="tier t1">
    <div class="tier-head wave"><svg viewBox="0 0 100 40" preserveAspectRatio="none"><path d="M0 0H100V28Q50 44 0 28Z" fill="#0c2d57"/></svg><b>TIER 1</b></div>
    <div class="price">$.02</div><div class="sub">(Lorem ipsum)</div>
    <ul class="feats"><li><svg viewBox="0 0 4 4" fill="none" stroke-width=".5"><rect x=".3" y=".3" width="3.4" height="3.4"/><path d="M1 2l.8.8L3 1.2"/></svg>Sed ut perspiciatis unde</li><li><svg viewBox="0 0 4 4" fill="none" stroke-width=".5"><rect x=".3" y=".3" width="3.4" height="3.4"/><path d="M1 2l.8.8L3 1.2"/></svg>Sed ut perspiciatis unde</li><li><svg viewBox="0 0 4 4" fill="none" stroke-width=".5"><rect x=".3" y=".3" width="3.4" height="3.4"/><path d="M1 2l.8.8L3 1.2"/></svg>Sed ut perspiciatis unde</li><li><svg viewBox="0 0 4 4" fill="none" stroke-width=".5"><rect x=".3" y=".3" width="3.4" height="3.4"/><path d="M1 2l.8.8L3 1.2"/></svg>Sed ut perspiciatis unde</li></ul>
    <div class="note">Lorem ipsum dolor<br>consectetur adipiscing</div>
    <div class="btn dark sq">Read More</div>
  </div>
  <div class="tier gold">
    <div class="tier-head wave"><svg viewBox="0 0 100 40" preserveAspectRatio="none"><path d="M0 0H100V22Q50 48 0 30Z" fill="#0aa5e2"/></svg><b>GOLD</b></div>
    <div class="price">$.04</div><div class="sub">(Lorem ipsum)</div>
    <ul class="feats"><li><svg viewBox="0 0 4 4" fill="none" stroke="#333" stroke-width=".5"><rect x=".3" y=".3" width="3.4" height="3.4"/><path d="M1 2l.8.8L3 1.2"/></svg>Sed ut perspiciatis unde</li><li><svg viewBox="0 0 4 4" fill="none" stroke="#333" stroke-width=".5"><rect x=".3" y=".3" width="3.4" height="3.4"/><path d="M1 2l.8.8L3 1.2"/></svg>Sed ut perspiciatis unde</li><li><svg viewBox="0 0 4 4" fill="none" stroke="#333" stroke-width=".5"><rect x=".3" y=".3" width="3.4" height="3.4"/><path d="M1 2l.8.8L3 1.2"/></svg>Sed ut perspiciatis unde</li><li><svg viewBox="0 0 4 4" fill="none" stroke="#333" stroke-width=".5"><rect x=".3" y=".3" width="3.4" height="3.4"/><path d="M1 2l.8.8L3 1.2"/></svg>Sed ut perspiciatis unde</li><li><svg viewBox="0 0 4 4" fill="none" stroke="#333" stroke-width=".5"><rect x=".3" y=".3" width="3.4" height="3.4"/><path d="M1 2l.8.8L3 1.2"/></svg>Sed ut perspiciatis unde</li><li><svg viewBox="0 0 4 4" fill="none" stroke="#333" stroke-width=".5"><rect x=".3" y=".3" width="3.4" height="3.4"/><path d="M1 2l.8.8L3 1.2"/></svg>Sed ut perspiciatis unde</li><li><svg viewBox="0 0 4 4" fill="none" stroke="#333" stroke-width=".5"><rect x=".3" y=".3" width="3.4" height="3.4"/><path d="M1 2l.8.8L3 1.2"/></svg>Sed ut perspiciatis unde</li></ul>
    <div class="btn sq">Read More</div>
  </div>
  <div class="tier plat">
    <div class="tier-head wave"><svg viewBox="0 0 100 40" preserveAspectRatio="none"><path d="M0 0H100V30Q50 42 0 24Z" fill="#0c2d57"/></svg><b>PLATINUM</b></div>
    <div class="price">$.06</div><div class="sub">(Lorem ipsum)</div>
    <ul class="feats"><li><svg viewBox="0 0 4 4" fill="none" stroke="#0aa5e2" stroke-width=".5"><rect x=".3" y=".3" width="3.4" height="3.4"/><path d="M1 2l.8.8L3 1.2"/></svg>Sed ut perspiciatis unde</li><li><svg viewBox="0 0 4 4" fill="none" stroke="#0aa5e2" stroke-width=".5"><rect x=".3" y=".3" width="3.4" height="3.4"/><path d="M1 2l.8.8L3 1.2"/></svg>Sed ut perspiciatis unde</li><li><svg viewBox="0 0 4 4" fill="none" stroke="#0aa5e2" stroke-width=".5"><rect x=".3" y=".3" width="3.4" height="3.4"/><path d="M1 2l.8.8L3 1.2"/></svg>Sed ut perspiciatis unde</li><li><svg viewBox="0 0 4 4" fill="none" stroke="#0aa5e2" stroke-width=".5"><rect x=".3" y=".3" width="3.4" height="3.4"/><path d="M1 2l.8.8L3 1.2"/></svg>Sed ut perspiciatis unde</li><li><svg viewBox="0 0 4 4" fill="none" stroke="#0aa5e2" stroke-width=".5"><rect x=".3" y=".3" width="3.4" height="3.4"/><path d="M1 2l.8.8L3 1.2"/></svg>Sed ut perspiciatis unde</li><li><svg viewBox="0 0 4 4" fill="none" stroke="#0aa5e2" stroke-width=".5"><rect x=".3" y=".3" width="3.4" height="3.4"/><path d="M1 2l.8.8L3 1.2"/></svg>Sed ut perspiciatis unde</li><li><svg viewBox="0 0 4 4" fill="none" stroke="#0aa5e2" stroke-width=".5"><rect x=".3" y=".3" width="3.4" height="3.4"/><path d="M1 2l.8.8L3 1.2"/></svg>Sed ut perspiciatis unde</li></ul>
    <div class="btn dark sq">Read More</div>
  </div>

  <h2 class="h2 center blog-title">Our <span>Blog</span></h2>
  <article class="card b1"><div class="card-img" role="img" aria-label="Photo of a man on a headset at a monitor"></div><p class="card-copy">Lorem ipsum dolor sit amet, consectetur adipiscing elit, sed do ...</p><div class="avatar"></div><div class="author">AVERY LANE</div><div class="btn">View Details</div></article>
  <article class="card b2"><div class="card-img" role="img" aria-label="Article graphic comparing two workflow diagrams"></div><p class="card-copy">Lorem ipsum dolor sit amet, consectetur adipiscing elit, sed do ...</p><div class="avatar"></div><div class="author">AVERY LANE</div><div class="btn">View Details</div></article>
  <article class="card b3"><div class="card-img" role="img" aria-label="Article banner about call center coaching over a keyboard"></div><p class="card-copy">Lorem ipsum dolor sit amet, consectetur adipiscing elit, sed do ...</p><div class="avatar"></div><div class="author">AVERY LANE</div><div class="btn">View Details</div></article>

  <h2 class="h2 contact-title">Contact <span>Us</span></h2>
  <div class="field f1">First Name *</div><div class="field f2">Last Name *</div><div class="field f3">Phone Number *</div><div class="field f4">Email *</div><div class="field f5">Comment or Message *</div>
  <div class="btn sq submit">Submit <i></i></div>
  <h2 class="h2 touch-title">Get In <span>Touch</span></h2>
  <p class="copy touch-copy">Sed ut perspiciatis unde omnis iste natus error sit voluptatem accusantium doloremque laudantium, totam rem aperiam, eaque ipsa quae ab illo inventore veritatis et quasi architecto beatae vitae dicta sunt explicabo.</p>
  <div class="info">
    <div><strong><svg viewBox="0 0 4 4"><path d="M2 0a1.4 1.4 0 0 1 1.4 1.4C3.4 2.4 2 4 2 4S.6 2.4.6 1.4A1.4 1.4 0 0 1 2 0z"/></svg>Find us at the office</strong><span>4410 Harbor Ave. Lindale, CA 90418</span></div>
    <div><strong><svg viewBox="0 0 4 4"><path d="M.5.5h1l.5 1-.6.5a2.5 2.5 0 0 0 1.1 1.1l.5-.6 1 .5v1C2 4 0 2 .5.5z"/></svg>Give us a ring</strong><span>Phone: 555-014-2290</span></div>
    <div><strong><svg viewBox="0 0 4 4"><path d="M0 1h4v2.5H0zM0 1l2 1.4L4 1"/></svg>Give us a Mail</strong><span>General: hello@dialmetric.com</span></div>
  </div>

  <footer class="footer">
    <div class="f-logo">DialMetric</div>
    <div class="social"><i></i><i></i><i></i><i></i></div>
    <div class="news"><div class="f-h">SIGN UP FOR NEWSLETTER</div><p>Excepteur sint occaecat cupidatat non proident, sunt in culpa qui officia deserunt</p><div class="in">Enter email</div><div class="btn">Subscription</div></div>
    <div class="fcontact"><div class="f-h">CONTACT US</div><div><svg viewBox="0 0 4 4"><circle cx="2" cy="2" r="1.6"/></svg>4410 Harbor Ave.<br>Lindale, CA 90418</div><div><svg viewBox="0 0 4 4"><circle cx="2" cy="2" r="1.6"/></svg>Phone: 555-014-2290</div><div><svg viewBox="0 0 4 4"><circle cx="2" cy="2" r="1.6"/></svg>Email: hello@dialmetric.com</div></div>
    <div class="links"><div class="f-h">QUICK LINKS</div><ul><li>Home</li><li>Industries</li><li>Services</li><li>Pricing</li><li>Team</li><li>Blog</li><li>Contact Us</li></ul></div>
    <div class="copyright">Copyright © DialMetric 2019. All rights reserved.</div>
  </footer>
</section>

<!-- Variation 2 -->
<section class="page v2">
  <svg class="hero-bg" viewBox="0 0 279 150"><path d="M118 0C112 60 106 112 132 126L279 150V0Z" fill="#0aa5e2"/></svg>
  <div class="logo">DialMetric</div>
  <nav class="nav on-blue"><span class="active">Home</span><span>Industries</span><span>Services</span><span>Pricing</span><span>Team</span><span>Blog</span><span>Contact Us</span></nav>
  <div class="register">Register / Login</div>
  <h1 class="hero-title">DialMetric</h1>
  <p class="hero-copy">Sed ut perspiciatis unde omnis iste natus error voluptatem accusantium doloremque eatae vitae dicta sunt explicabo.</p>
  <div class="btn dark hero-btn">Get Started <i></i></div>
  <div class="hero-art" role="img" aria-label="Illustration of an agent working at a laptop beside floating screens"></div>
  <svg class="mouse" viewBox="0 0 6 14"><rect x="1" y="0.5" width="4" height="7" rx="2" fill="none" stroke="#333" stroke-width=".5"/><path d="M1.5 10l1.5 1.5 1.5-1.5" fill="none" stroke="#333" stroke-width=".5"/></svg>

  <h2 class="h2 center welcome-title">Welcome to <span>DialMetric</span></h2>
  <p class="copy c welcome-copy">Sed ut perspiciatis unde omnis iste natus error sit voluptatem accusantium doloremque laudantium, totam rem aperiam, eaque ipsa quae ab illo inventore veritatis et quasi architecto beatae vitae dicta sunt explicabo.</p>

  <h2 class="h2 ind-title">Our <span>Industries</span></h2>
  <p class="copy ind-copy">Sed ut perspiciatis unde omnis iste natus error sit voluptatem accusantium doloremque laudantium, totam rem aperiam, eaque ipsa quae ab illo inventore veritatis et quasi architecto beatae vitae dicta sunt explicabo. Nemo enim ipsam voluptatem quia voluptas sit aspernatur aut odit aut fugit, sed quia consequuntur magni dolores eos qui nesciunt.</p>
  <div class="btn ind-btn">Read More <i></i></div>
  <div class="ind-art" role="img" aria-label="Illustration of a woman at a laptop in front of a large monitor"></div>

  <div class="srv-art" role="img" aria-label="Illustration of a support agent with headset surrounded by service icons"></div>
  <h2 class="h2 srv-title">Our <span>Services</span></h2>
  <p class="copy srv-copy">Sed ut perspiciatis unde omnis iste natus error sit voluptatem accusantium doloremque laudantium, totam rem aperiam, eaque ipsa quae ab illo inventore veritatis et quasi architecto beatae vitae dicta sunt explicabo. Nemo enim ipsam voluptatem quia voluptas sit aspernatur aut odit aut fugit, sed quia consequuntur magni dolores eos qui nesciunt.</p>
  <div class="btn srv-btn">View More <i></i></div>

  <h2 class="h2 team-title">Our <span>Team</span></h2>
  <p class="copy team-copy">Sed ut perspiciatis unde omnis iste natus error sit voluptatem accusantium doloremque laudantium, totam rem aperiam, eaque ipsa quae ab illo inventore veritatis et quasi architecto beatae vitae dicta sunt explicabo. Nemo enim ipsam voluptatem quia voluptas sit aspernatur aut odit aut fugit, sed quia consequuntur magni dolores eos qui nesciunt.</p>
  <div class="btn team-btn">View More <i></i></div>
  <div class="team-art" role="img" aria-label="Illustration of team member portraits arranged around a circle"></div>

  <h2 class="h2 center price-title">Our <span>Pricing</span></h2>
  <p class="copy c price-copy">Sed ut perspiciatis unde omnis iste natus error sit voluptatem accusantium doloremque laudantium, totam rem aperiam, eaque ipsa quae ab illo inventore veritatis et quasi architecto beatae vitae dicta sunt explicabo.</p>
  <div class="tier t1">
    <div class="tier-head">TIER 1</div>
    <div class="price">$.02</div><div class="sub">(Lorem ipsum)</div>
    <ul class="feats"><li><svg viewBox="0 0 4 4" fill="none" stroke-width=".5"><rect x=".3" y=".3" width="3.4" height="3.4"/><path d="M1 2l.8.8L3 1.2"/></svg>Sed ut perspiciatis unde</li><li><svg viewBox="0 0 4 4" fill="none" stroke-width=".5"><rect x=".3" y=".3" width="3.4" height="3.4"/><path d="M1 2l.8.8L3 1.2"/></svg>Sed ut perspiciatis unde</li><li><svg viewBox="0 0 4 4" fill="none" stroke-width=".5"><rect x=".3" y=".3" width="3.4" height="3.4"/><path d="M1 2l.8.8L3 1.2"/></svg>Sed ut perspiciatis unde</li><li><svg viewBox="0 0 4 4" fill="none" stroke-width=".5"><rect x=".3" y=".3" width="3.4" height="3.4"/><path d="M1 2l.8.8L3 1.2"/></svg>Sed ut perspiciatis unde</li></ul>
    <div class="note">Lorem ipsum dolor<br>consectetur adipiscing</div>
    <div class="btn dark sq">Read More</div>
  </div>
  <div class="tier gold">
    <div class="tier-head">GOLD</div>
    <div class="price">$.04</div><div class="sub">(Lorem ipsum)</div>
    <ul class="feats"><li><svg viewBox="0 0 4 4" fill="none" stroke="#333" stroke-width=".5"><rect x=".3" y=".3" width="3.4" height="3.4"/><path d="M1 2l.8.8L3 1.2"/></svg>Sed ut perspiciatis unde</li><li><svg viewBox="0 0 4 4" fill="none" stroke="#333" stroke-width=".5"><rect x=".3" y=".3" width="3.4" height="3.4"/><path d="M1 2l.8.8L3 1.2"/></svg>Sed ut perspiciatis unde</li><li><svg viewBox="0 0 4 4" fill="none" stroke="#333" stroke-width=".5"><rect x=".3" y=".3" width="3.4" height="3.4"/><path d="M1 2l.8.8L3 1.2"/></svg>Sed ut perspiciatis unde</li><li><svg viewBox="0 0 4 4" fill="none" stroke="#333" stroke-width=".5"><rect x=".3" y=".3" width="3.4" height="3.4"/><path d="M1 2l.8.8L3 1.2"/></svg>Sed ut perspiciatis unde</li><li><svg viewBox="0 0 4 4" fill="none" stroke="#333" stroke-width=".5"><rect x=".3" y=".3" width="3.4" height="3.4"/><path d="M1 2l.8.8L3 1.2"/></svg>Sed ut perspiciatis unde</li><li><svg viewBox="0 0 4 4" fill="none" stroke="#333" stroke-width=".5"><rect x=".3" y=".3" width="3.4" height="3.4"/><path d="M1 2l.8.8L3 1.2"/></svg>Sed ut perspiciatis unde</li><li><svg viewBox="0 0 4 4" fill="none" stroke="#333" stroke-width=".5"><rect x=".3" y=".3" width="3.4" height="3.4"/><path d="M1 2l.8.8L3 1.2"/></svg>Sed ut perspiciatis unde</li></ul>
    <div class="btn sq">Read More</div>
  </div>
  <div class="tier plat">
    <div class="tier-head">PLATINUM</div>
    <div class="price">$.06</div><div class="sub">(Lorem ipsum)</div>
    <ul class="feats"><li><svg viewBox="0 0 4 4" fill="none" stroke="#0aa5e2" stroke-width=".5"><rect x=".3" y=".3" width="3.4" height="3.4"/><path d="M1 2l.8.8L3 1.2"/></svg>Sed ut perspiciatis unde</li><li><svg viewBox="0 0 4 4" fill="none" stroke="#0aa5e2" stroke-width=".5"><rect x=".3" y=".3" width="3.4" height="3.4"/><path d="M1 2l.8.8L3 1.2"/></svg>Sed ut perspiciatis unde</li><li><svg viewBox="0 0 4 4" fill="none" stroke="#0aa5e2" stroke-width=".5"><rect x=".3" y=".3" width="3.4" height="3.4"/><path d="M1 2l.8.8L3 1.2"/></svg>Sed ut perspiciatis unde</li><li><svg viewBox="0 0 4 4" fill="none" stroke="#0aa5e2" stroke-width=".5"><rect x=".3" y=".3" width="3.4" height="3.4"/><path d="M1 2l.8.8L3 1.2"/></svg>Sed ut perspiciatis unde</li><li><svg viewBox="0 0 4 4" fill="none" stroke="#0aa5e2" stroke-width=".5"><rect x=".3" y=".3" width="3.4" height="3.4"/><path d="M1 2l.8.8L3 1.2"/></svg>Sed ut perspiciatis unde</li><li><svg viewBox="0 0 4 4" fill="none" stroke="#0aa5e2" stroke-width=".5"><rect x=".3" y=".3" width="3.4" height="3.4"/><path d="M1 2l.8.8L3 1.2"/></svg>Sed ut perspiciatis unde</li><li><svg viewBox="0 0 4 4" fill="none" stroke="#0aa5e2" stroke-width=".5"><rect x=".3" y=".3" width="3.4" height="3.4"/><path d="M1 2l.8.8L3 1.2"/></svg>Sed ut perspiciatis unde</li></ul>
    <div class="btn dark sq">Read More</div>
  </div>

  <h2 class="h2 center blog-title">Our <span>Blog</span></h2>
  <article class="card b1"><div class="card-img" role="img" aria-label="Photo of a man on a headset at a monitor"></div><p class="card-copy">Lorem ipsum dolor sit amet, consectetur adipiscing elit, sed do ...</p><div class="avatar"></div><div class="author">AVERY LANE</div><div class="btn">View Details</div></article>
  <article class="card b2"><div class="card-img" role="img" aria-label="Article graphic comparing two workflow diagrams"></div><p class="card-copy">Lorem ipsum dolor sit amet, consectetur adipiscing elit, sed do ...</p><div class="avatar"></div><div class="author">AVERY LANE</div><div class="btn">View Details</div></article>
  <article class="card b3"><div class="card-img" role="img" aria-label="Article banner about call center coaching over a keyboard"></div><p class="card-copy">Lorem ipsum dolor sit amet, consectetur adipiscing elit, sed do ...</p><div class="avatar"></div><div class="author">AVERY LANE</div><div class="btn">View Details</div></article>

  <h2 class="h2 contact-title">Contact <span>Us</span></h2>
  <div class="field f1">First Name *</div><div class="field f2">Last Name *</div><div class="field f3">Phone Number *</div><div class="field f4">Email *</div><div class="field f5">Comment or Message *</div>
  <div class="btn sq submit">Submit <i></i></div>
  <h2 class="h2 touch-title">Get In <span>Touch</span></h2>
  <p class="copy touch-copy">Sed ut perspiciatis unde omnis iste natus error sit voluptatem accusantium doloremque laudantium, totam rem aperiam, eaque ipsa quae ab illo inventore veritatis et quasi architecto beatae vitae dicta sunt explicabo.</p>
  <div class="info">
    <div><strong><svg viewBox="0 0 4 4"><path d="M2 0a1.4 1.4 0 0 1 1.4 1.4C3.4 2.4 2 4 2 4S.6 2.4.6 1.4A1.4 1.4 0 0 1 2 0z"/></svg>Find us at the office</strong><span>4410 Harbor Ave. Lindale, CA 90418</span></div>
    <div><strong><svg viewBox="0 0 4 4"><path d="M.5.5h1l.5 1-.6.5a2.5 2.5 0 0 0 1.1 1.1l.5-.6 1 .5v1C2 4 0 2 .5.5z"/></svg>Give us a ring</strong><span>Phone: 555-014-2290</span></div>
    <div><strong><svg viewBox="0 0 4 4"><path d="M0 1h4v2.5H0zM0 1l2 1.4L4 1"/></svg>Give us a Mail</strong><span>General: hello@dialmetric.com</span></div>
  </div>

  <footer class="footer">
    <div class="f-logo">DialMetric</div>
    <div class="social"><i></i><i></i><i></i><i></i></div>
    <div class="news"><div class="f-h">SIGN UP FOR NEWSLETTER</div><p>Excepteur sint occaecat cupidatat non proident, sunt in culpa qui officia deserunt</p><div class="in">Enter email</div><div class="btn">Subscription</div></div>
    <div class="fcontact"><div class="f-h">CONTACT US</div><div><svg viewBox="0 0 4 4"><circle cx="2" cy="2" r="1.6"/></svg>4410 Harbor Ave.<br>Lindale, CA 90418</div><div><svg viewBox="0 0 4 4"><circle cx="2" cy="2" r="1.6"/></svg>Phone: 555-014-2290</div><div><svg viewBox="0 0 4 4"><circle cx="2" cy="2" r="1.6"/></svg>Email: hello@dialmetric.com</div></div>
    <div class="links"><div class="f-h">QUICK LINKS</div><ul><li>Home</li><li>Industries</li><li>Services</li><li>Pricing</li><li>Team</li><li>Blog</li><li>Contact Us</li></ul></div>
    <div class="copyright">Copyright © DialMetric 2019. All rights reserved.</div>
  </footer>
</section>

<!-- Variation 3 -->
<section class="page v3">
  <svg class="hero-bg" viewBox="0 0 279 150"><rect x="0" y="20" width="279" height="130" fill="#0aa5e2"/></svg>
  <div class="logo">DialMetric</div>
  <nav class="nav"><span class="active">Home</span><span>Industries</span><span>Services</span><span>Pricing</span><span>Team</span><span>Blog</span><span>Contact Us</span></nav>
  <div class="register">Register / Login</div>
  <h1 class="hero-title">DialMetric</h1>
  <p class="hero-copy">Sed ut perspiciatis unde omnis iste natus error voluptatem accusantium doloremque eatae vitae dicta sunt explicabo.</p>
  <div class="btn dark hero-btn">Get Started <i></i></div>
  <div class="hero-art" role="img" aria-label="Illustration of an agent working at a laptop beside floating screens"></div>
  <svg class="mouse" viewBox="0 0 6 14"><rect x="1" y="0.5" width="4" height="7" rx="2" fill="none" stroke="#fff" stroke-width=".5"/><path d="M1.5 10l1.5 1.5 1.5-1.5" fill="none" stroke="#fff" stroke-width=".5"/></svg>

  <h2 class="h2 center welcome-title">Welcome to <span>DialMetric</span></h2>
  <p class="copy c welcome-copy">Sed ut perspiciatis unde omnis iste natus error sit voluptatem accusantium doloremque laudantium, totam rem aperiam, eaque ipsa quae ab illo inventore veritatis et quasi architecto beatae vitae dicta sunt explicabo.</p>

  <h2 class="h2 ind-title">Our <span>Industries</span></h2>
  <p class="copy ind-copy">Sed ut perspiciatis unde omnis iste natus error sit voluptatem accusantium doloremque laudantium, totam rem aperiam, eaque ipsa quae ab illo inventore veritatis et quasi architecto beatae vitae dicta sunt explicabo. Nemo enim ipsam voluptatem quia voluptas sit aspernatur aut odit aut fugit, sed quia consequuntur magni dolores eos qui nesciunt.</p>
  <div class="btn ind-btn">Read More <i></i></div>
  <div class="ind-art" role="img" aria-label="Illustration of a woman at a laptop in front of a large monitor"></div>

  <div class="srv-art" role="img" aria-label="Illustration of a support agent with headset surrounded by service icons"></div>
  <h2 class="h2 srv-title">Our <span>Services</span></h2>
  <p class="copy srv-copy">Sed ut perspiciatis unde omnis iste natus error sit voluptatem accusantium doloremque laudantium, totam rem aperiam, eaque ipsa quae ab illo inventore veritatis et quasi architecto beatae vitae dicta sunt explicabo. Nemo enim ipsam voluptatem quia voluptas sit aspernatur aut odit aut fugit, sed quia consequuntur magni dolores eos qui nesciunt.</p>
  <div class="btn srv-btn">View More <i></i></div>

  <h2 class="h2 team-title">Our <span>Team</span></h2>
  <p class="copy team-copy">Sed ut perspiciatis unde omnis iste natus error sit voluptatem accusantium doloremque laudantium, totam rem aperiam, eaque ipsa quae ab illo inventore veritatis et quasi architecto beatae vitae dicta sunt explicabo. Nemo enim ipsam voluptatem quia voluptas sit aspernatur aut odit aut fugit, sed quia consequuntur magni dolores eos qui nesciunt.</p>
  <div class="btn team-btn">View More <i></i></div>
  <div class="team-art" role="img" aria-label="Illustration of team member portraits arranged around a circle"></div>

  <h2 class="h2 center price-title">Our <span>Pricing</span></h2>
  <p class="copy c price-copy">Sed ut perspiciatis unde omnis iste natus error sit voluptatem accusantium doloremque laudantium, totam rem aperiam, eaque ipsa quae ab illo inventore veritatis et quasi architecto beatae vitae dicta sunt explicabo.</p>
  <div class="tier t1">
    <div class="tier-head">TIER 1</div>
    <div class="price">$.02</div><div class="sub">(Lorem ipsum)</div>
    <ul class="feats"><li><svg viewBox="0 0 4 4" fill="none" stroke-width=".5"><rect x=".3" y=".3" width="3.4" height="3.4"/><path d="M1 2l.8.8L3 1.2"/></svg>Sed ut perspiciatis unde</li><li><svg viewBox="0 0 4 4" fill="none" stroke-width=".5"><rect x=".3" y=".3" width="3.4" height="3.4"/><path d="M1 2l.8.8L3 1.2"/></svg>Sed ut perspiciatis unde</li><li><svg viewBox="0 0 4 4" fill="none" stroke-width=".5"><rect x=".3" y=".3" width="3.4" height="3.4"/><path d="M1 2l.8.8L3 1.2"/></svg>Sed ut perspiciatis unde</li><li><svg viewBox="0 0 4 4" fill="none" stroke-width=".5"><rect x=".3" y=".3" width="3.4" height="3.4"/><path d="M1 2l.8.8L3 1.2"/></svg>Sed ut perspiciatis unde</li></ul>
    <div class="note">Lorem ipsum dolor<br>consectetur adipiscing</div>
    <div class="btn dark sq">Read More</div>
  </div>
  <div class="tier gold">
    <div class="tier-head">GOLD</div>
    <div class="price">$.04</div><div class="sub">(Lorem ipsum)</div>
    <ul class="feats"><li><svg viewBox="0 0 4 4" fill="none" stroke="#333" stroke-width=".5"><rect x=".3" y=".3" width="3.4" height="3.4"/><path d="M1 2l.8.8L3 1.2"/></svg>Sed ut perspiciatis unde</li><li><svg viewBox="0 0 4 4" fill="none" stroke="#333" stroke-width=".5"><rect x=".3" y=".3" width="3.4" height="3.4"/><path d="M1 2l.8.8L3 1.2"/></svg>Sed ut perspiciatis unde</li><li><svg viewBox="0 0 4 4" fill="none" stroke="#333" stroke-width=".5"><rect x=".3" y=".3" width="3.4" height="3.4"/><path d="M1 2l.8.8L3 1.2"/></svg>Sed ut perspiciatis unde</li><li><svg viewBox="0 0 4 4" fill="none" stroke="#333" stroke-width=".5"><rect x=".3" y=".3" width="3.4" height="3.4"/><path d="M1 2l.8.8L3 1.2"/></svg>Sed ut perspiciatis unde</li><li><svg viewBox="0 0 4 4" fill="none" stroke="#333" stroke-width=".5"><rect x=".3" y=".3" width="3.4" height="3.4"/><path d="M1 2l.8.8L3 1.2"/></svg>Sed ut perspiciatis unde</li><li><svg viewBox="0 0 4 4" fill="none" stroke="#333" stroke-width=".5"><rect x=".3" y=".3" width="3.4" height="3.4"/><path d="M1 2l.8.8L3 1.2"/></svg>Sed ut perspiciatis unde</li><li><svg viewBox="0 0 4 4" fill="none" stroke="#333" stroke-width=".5"><rect x=".3" y=".3" width="3.4" height="3.4"/><path d="M1 2l.8.8L3 1.2"/></svg>Sed ut perspiciatis unde</li></ul>
    <div class="btn sq">Read More</div>
  </div>
  <div class="tier plat">
    <div class="tier-head">PLATINUM</div>
    <div class="price">$.06</div><div class="sub">(Lorem ipsum)</div>
    <ul class="feats"><li><svg viewBox="0 0 4 4" fill="none" stroke="#0aa5e2" stroke-width=".5"><rect x=".3" y=".3" width="3.4" height="3.4"/><path d="M1 2l.8.8L3 1.2"/></svg>Sed ut perspiciatis unde</li><li><svg viewBox="0 0 4 4" fill="none" stroke="#0aa5e2" stroke-width=".5"><rect x=".3" y=".3" width="3.4" height="3.4"/><path d="M1 2l.8.8L3 1.2"/></svg>Sed ut perspiciatis unde</li><li><svg viewBox="0 0 4 4" fill="none" stroke="#0aa5e2" stroke-width=".5"><rect x=".3" y=".3" width="3.4" height="3.4"/><path d="M1 2l.8.8L3 1.2"/></svg>Sed ut perspiciatis unde</li><li><svg viewBox="0 0 4 4" fill="none" stroke="#0aa5e2" stroke-width=".5"><rect x=".3" y=".3" width="3.4" height="3.4"/><path d="M1 2l.8.8L3 1.2"/></svg>Sed ut perspiciatis unde</li><li><svg viewBox="0 0 4 4" fill="none" stroke="#0aa5e2" stroke-width=".5"><rect x=".3" y=".3" width="3.4" height="3.4"/><path d="M1 2l.8.8L3 1.2"/></svg>Sed ut perspiciatis unde</li><li><svg viewBox="0 0 4 4" fill="none" stroke="#0aa5e2" stroke-width=".5"><rect x=".3" y=".3" width="3.4" height="3.4"/><path d="M1 2l.8.8L3 1.2"/></svg>Sed ut perspiciatis unde</li><li><svg viewBox="0 0 4 4" fill="none" stroke="#0aa5e2" stroke-width=".5"><rect x=".3" y=".3" width="3.4" height="3.4"/><path d="M1 2l.8.8L3 1.2"/></svg>Sed ut perspiciatis unde</li></ul>
    <div class="btn dark sq">Read More</div>
  </div>

  <h2 class="h2 center blog-title">Our <span>Blog</span></h2>
  <article class="card b1"><div class="card-img" role="img" aria-label="Photo of a man on a headset at a monitor"></div><p class="card-copy">Lorem ipsum dolor sit amet, consectetur adipiscing elit, sed do ...</p><div class="avatar"></div><div class="author">AVERY LANE</div><div class="btn">View Details</div></article>
  <article class="card b2"><div class="card-img" role="img" aria-label="Article graphic comparing two workflow diagrams"></div><p class="card-copy">Lorem ipsum dolor sit amet, consectetur adipiscing elit, sed do ...</p><div class="avatar"></div><div class="author">AVERY LANE</div><div class="btn">View Details</div></article>
  <article class="card b3"><div class="card-img" role="img" aria-label="Article banner about call center coaching over a keyboard"></div><p class="card-copy">Lorem ipsum dolor sit amet, consectetur adipiscing elit, sed do ...</p><div class="avatar"></div><div class="author">AVERY LANE</div><div class="btn">View Details</div></article>

  <h2 class="h2 contact-title">Contact <span>Us</span></h2>
  <div class="field f1">First Name *</div><div class="field f2">Last Name *</div><div class="field f3">Phone Number *</div><div class="field f4">Email *</div><div class="field f5">Comment or Message *</div>
  <div class="btn sq submit">Submit <i></i></div>
  <h2 class="h2 touch-title">Get In <span>Touch</span></h2>
  <p class="copy touch-copy">Sed ut perspiciatis unde omnis iste natus error sit voluptatem accusantium doloremque laudantium, totam rem aperiam, eaque ipsa quae ab illo inventore veritatis et quasi architecto beatae vitae dicta sunt explicabo.</p>
  <div class="info">
    <div><strong><svg viewBox="0 0 4 4"><path d="M2 0a1.4 1.4 0 0 1 1.4 1.4C3.4 2.4 2 4 2 4S.6 2.4.6 1.4A1.4 1.4 0 0 1 2 0z"/></svg>Find us at the office</strong><span>4410 Harbor Ave. Lindale, CA 90418</span></div>
    <div><strong><svg viewBox="0 0 4 4"><path d="M.5.5h1l.5 1-.6.5a2.5 2.5 0 0 0 1.1 1.1l.5-.6 1 .5v1C2 4 0 2 .5.5z"/></svg>Give us a ring</strong><span>Phone: 555-014-2290</span></div>
    <div><strong><svg viewBox="0 0 4 4"><path d="M0 1h4v2.5H0zM0 1l2 1.4L4 1"/></svg>Give us a Mail</strong><span>General: hello@dialmetric.com</span></div>
  </div>

  <footer class="footer">
    <div class="f-logo">DialMetric</div>
    <div class="social"><i></i><i></i><i></i><i></i></div>
    <div class="news"><div class="f-h">SIGN UP FOR NEWSLETTER</div><p>Excepteur sint occaecat cupidatat non proident, sunt in culpa qui officia deserunt</p><div class="in">Enter email</div><div class="btn">Subscription</div></div>
    <div class="fcontact"><div class="f-h">CONTACT US</div><div><svg viewBox="0 0 4 4"><circle cx="2" cy="2" r="1.6"/></svg>4410 Harbor Ave.<br>Lindale, CA 90418</div><div><svg viewBox="0 0 4 4"><circle cx="2" cy="2" r="1.6"/></svg>Phone: 555-014-2290</div><div><svg viewBox="0 0 4 4"><circle cx="2" cy="2" r="1.6"/></svg>Email: hello@dialmetric.com</div></div>
    <div class="links"><div class="f-h">QUICK LINKS</div><ul><li>Home</li><li>Industries</li><li>Services</li><li>Pricing</li><li>Team</li><li>Blog</li><li>Contact Us</li></ul></div>
    <div class="copyright">Copyright © DialMetric 2019. All rights reserved.</div>
  </footer>
</section>

</body>
</html>
```